3 Page Design for Ninth Bay Capital

We want a Home Page, About Page, and Products & Services Page for Ninth Bay Capital. Please refer to the attached docs for more info.
If done in Figma, would like Figma files that can easily be ported to Wordpress.

```html
<!DOCTYPE html>
<html lang="en">
<head>
<meta charset="UTF-8">
<title>Ninth Bay Capital — Home</title>
<link href="https://fonts.googleapis.com/css2?family=Poppins:wght@400;500;600;700&display=swap" rel="stylesheet">
<style>
  :root {
    --ink: #2b2b2b;
    --white: #ffffff;
    --sand: #e8dcc8;
    --cream: #fbf2e5;
    --bronze: #8b7355;
    --purple: #6e5a9a;
    --crimson: #9b1b30;
    --hero-dark: #2a1f18;
    --hero-warm: #6a4a32;
  }
  * { box-sizing: border-box; margin: 0; padding: 0; }
  html, body { width: 1200px; height: 2621px; overflow: hidden; }
  body { font-family: "Poppins", sans-serif; color: var(--ink); position: relative; background: var(--white); }
  .btn {
    position: absolute; display: flex; align-items: center; justify-content: center;
    color: var(--white); font-weight: 600; font-size: 16px; border-radius: 3px; text-decoration: none;
  }
  .btn--purple { background: var(--purple); }
  .btn--crimson { background: var(--crimson); font-size: 18px; }

  /* Hero */
  .hero { position: absolute; top: 0; left: 0; width: 1200px; height: 722px; }
  .hero__photo { position: absolute; inset: 0; background: linear-gradient(100deg, var(--hero-dark) 0%, var(--hero-warm) 45%, #8a6a50 65%, #3b2c22 100%); }
  .brand { position: absolute; left: 75px; top: 56px; display: flex; align-items: center; gap: 10px; color: var(--white); font-weight: 700; font-size: 15px; letter-spacing: .2px; }
  .brand__dot { width: 22px; height: 22px; border-radius: 50%; background: var(--white); }
  .nav { position: absolute; top: 62px; left: 673px; display: flex; gap: 40px; }
  .nav a { color: var(--white); font-size: 14px; font-weight: 600; text-decoration: none; text-transform: uppercase; }
  .nav a.is-active { border-bottom: 2px solid var(--white); padding-bottom: 2px; }
  .hero__title { position: absolute; left: 74px; top: 288px; color: var(--white); font-size: 54px; font-weight: 700; letter-spacing: .5px; }
  .hero__lead { position: absolute; left: 75px; top: 357px; width: 520px; color: var(--white); font-size: 25px; line-height: 33px; }

  /* Story */
  .story { position: absolute; top: 722px; left: 0; width: 1200px; height: 536px; background: var(--sand); }
  .story__photo { position: absolute; left: 74px; top: 78px; width: 692px; height: 380px; background: linear-gradient(135deg, #8c3a2a, #5a6f8e 55%, #b0462e); }
  .story__title { position: absolute; left: 793px; top: 108px; font-size: 40px; font-weight: 700; line-height: 44px; }
  .story__text { position: absolute; left: 793px; top: 217px; width: 310px; font-size: 16.5px; line-height: 26.5px; }

  /* Services */
  .services { position: absolute; top: 1258px; left: 0; width: 1200px; height: 542px; background: linear-gradient(var(--cream) 0 278px, var(--sand) 278px); }
  .services__title { position: absolute; top: 60px; width: 100%; text-align: center; font-size: 40px; font-weight: 700; }
  .card { position: absolute; top: 135px; width: 242px; height: 322px; background: var(--white); text-align: center; padding: 25px 22px 0; }
  .card__icon { width: 88px; height: 88px; border-radius: 50%; background: var(--sand); margin: 0 auto 14px; display: flex; align-items: center; justify-content: center; }
  .card__title { color: var(--purple); font-size: 20px; font-weight: 600; line-height: 26px; margin-bottom: 14px; }
  .card__text { font-size: 13.5px; line-height: 22.5px; }
  .card--featured { background: var(--bronze); }
  .card--featured .card__title, .card--featured .card__text { color: var(--white); }

  /* Mission */
  .mission { position: absolute; top: 1800px; left: 0; width: 1200px; height: 377px; background: var(--white); }
  .mission__title { position: absolute; left: 74px; width: 600px; top: 76px; text-align: center; font-size: 40px; font-weight: 700; }
  .mission__text { position: absolute; left: 94px; width: 560px; top: 140px; text-align: center; font-size: 17px; line-height: 32px; }
  .mission__photo { position: absolute; left: 705px; top: 58px; width: 422px; height: 263px; background: linear-gradient(135deg, #e8ecef, #c9d0d6 60%, #f3f4f5); }

  /* CTA */
  .cta { position: absolute; top: 2177px; left: 0; width: 1200px; height: 298px; background: var(--bronze); text-align: center; color: var(--white); }
  .cta__title { position: absolute; top: 62px; width: 100%; font-size: 40px; font-weight: 700; }
  .cta__lead { position: absolute; top: 121px; width: 100%; font-size: 18.5px; }

  /* Footer */
  .footer { position: absolute; top: 2475px; left: 0; width: 1200px; height: 146px; background: var(--sand); }
  .footer__nav { position: absolute; left: 73px; top: 45px; display: flex; gap: 40px; }
  .footer__nav a { color: var(--ink); font-size: 13.5px; font-weight: 600; text-decoration: none; text-transform: uppercase; }
  .footer__copy { position: absolute; left: 75px; top: 90px; font-size: 12px; }
  .social { position: absolute; left: 956px; top: 76px; display: flex; gap: 20px; }
  .social span { width: 22px; height: 22px; border-radius: 50%; background: var(--ink); display: block; }
</style>
</head>
<body>
  <header class="hero">
    <div class="hero__photo" role="img" aria-label="Smiling café owner in an apron holding a tablet in a warm-lit shop"></div>
    <div class="brand"><span class="brand__dot"></span>NINTH BAY CAPITAL</div>
    <nav class="nav">
      <a class="is-active" href="#">Home</a><a href="#">About</a><a href="#">Products &amp; Services</a><a href="#">Contact Us</a>
    </nav>
    <h1 class="hero__title">NINTH BAY CAPITAL</h1>
    <p class="hero__lead">Empowering athletes and entrepreneurs to build generational success — on and off the field</p>
    <a class="btn btn--purple" href="#" style="left:75px;top:481px;width:166px;height:51px;">Learn More</a>
  </header>

  <section class="story">
    <div class="story__photo" role="img" aria-label="Man in a suit stepping on a soccer ball beside a red brick building"></div>
    <h2 class="story__title">Company<br>Story</h2>
    <p class="story__text">Nemo enim ipsam voluptatem quia voluptas sit aspernatur aut odit aut fugit, sed quia consequuntur magni dolores eos qui ratione voluptatem sequi nesciunt.</p>
    <a class="btn btn--crimson" href="#" style="left:793px;top:372px;width:166px;height:51px;font-size:16px;">Learn More</a>
  </section>

  <section class="services">
    <h2 class="services__title">Product &amp; Services</h2>
    <article class="card" style="left:74px;">
      <div class="card__icon"><svg width="44" height="44" viewBox="0 0 44 44" fill="none" stroke="#2b2b2b" stroke-width="1.6"><path d="M6 34a16 16 0 0 1 32 0z"/><path d="M22 34l7-9"/><circle cx="22" cy="34" r="2"/></svg></div>
      <h3 class="card__title">Performance Coaching</h3>
      <p class="card__text">Sharpen your discipline, habits, and mental resilience with elite coaching inspired by the world of competitive sports.</p>
    </article>
    <article class="card card--featured" style="left:345px;">
      <div class="card__icon"><svg width="44" height="44" viewBox="0 0 44 44" fill="none" stroke="#9b1b30" stroke-width="1.6"><circle cx="22" cy="18" r="12"/><path d="M16 38h12M18 30h8v8h-8z"/></svg></div>
      <h3 class="card__title">Business &amp; Wealth Strategy</h3>
      <p class="card__text">Structure your business, manage your money smarter, and build long-term financial stability. From cash flow to investments.</p>
    </article>
    <article class="card" style="left:615px;">
      <div class="card__icon"><svg width="44" height="44" viewBox="0 0 44 44" fill="none" stroke="#2b2b2b" stroke-width="1.6"><rect x="6" y="20" width="16" height="16"/><rect x="24" y="6" width="14" height="14"/><path d="M28 26h6v6"/></svg></div>
      <h3 class="card__title">Wellness Optimization</h3>
      <p class="card__text">Elevate your physical, mental, and emotional well-being. We integrate nutrition, recovery, stress management and lifestyle systems.</p>
    </article>
    <article class="card" style="left:885px;">
      <div class="card__icon"><svg width="44" height="44" viewBox="0 0 44 44" fill="none" stroke="#2b2b2b" stroke-width="1.6"><circle cx="22" cy="22" r="6"/><circle cx="22" cy="22" r="13" stroke-dasharray="5 3"/><path d="M4 22a18 18 0 0 1 30-13M40 22a18 18 0 0 1-30 13"/></svg></div>
      <h3 class="card__title">Automation Systems</h3>
      <p class="card__text">Use cutting-edge automation and AI-driven workflows to streamline operations, reduce burnout, and scale faster.</p>
    </article>
  </section>

  <section class="mission">
    <h2 class="mission__title">Our Brand Mission</h2>
    <p class="mission__text">Ninth Bay bridges the worlds of performance, wealth, and wellness — helping athletes and entrepreneurs build lasting success on and off the field. It merges the discipline of sports, the structure of business, and the power of automation to create generational success.</p>
    <div class="mission__photo" role="img" aria-label="Athlete in a red top stretching on a white pedestrian bridge"></div>
  </section>

  <section class="cta">
    <h2 class="cta__title">Start Building Your Legacy</h2>
    <p class="cta__lead">Unlock the structure, discipline, and systems that create generational success.</p>
    <a class="btn btn--crimson" href="#" style="left:434px;top:172px;width:154px;height:53px;">Get Started</a>
    <a class="btn btn--crimson" href="#" style="left:616px;top:172px;width:154px;height:53px;">Book a Call</a>
  </section>

  <footer class="footer">
    <nav class="footer__nav">
      <a href="#">Home</a><a href="#">About</a><a href="#">Products &amp; Services</a><a href="#">Contact Us</a>
    </nav>
    <p class="footer__copy">Copyright 2025 © CompanyName&nbsp; All Right Reserved</p>
    <div class="social" aria-label="Social links">
      <span aria-label="Social link"></span><span aria-label="Social link"></span><span aria-label="Social link"></span><span aria-label="Social link"></span><span aria-label="Social link"></span>
    </div>
  </footer>
</body>
</html>
```